Building company buisness cards

We are looking for a sharp modern new look for our business cards.
We are a New Zealand based company that specialises in house and land packages.
We have attached a photo of the current logo and would like to see if it can be improved somehow if needed.
We are open to any colours but we have chosen green at this stage.
Feel free to change the font and make the logo smarter looking.
Play with the colours and see what looks best.

We want a card that looks so good know one will want to throw it away!

Target Market(s)

Home buyers

Industry/Entity Type

Building

Contact Information for Business Card

Derek Tolvane
0217394062
dtolvane@quillmarkhomesteads.co.nz
quillmarkhomesteads.co.nz

Font styles to use
Serif
Sans Serif

Colors

Designer to choose colors to be used in the design.

Requirements
Must have
• Logo and company name on one side, details on the other side
Nice to have
• Color codes for the original green are HEX #4a8028, RGB(74,128,40), CMYK(42,0,69,50)
• Round corners, Raised and/or spot UV

```html
<!DOCTYPE html>
<html lang="en">
<head>
<meta charset="utf-8">
<title>Quillmark Homesteads — Business Card</title>
<link href="https://fonts.googleapis.com/css2?family=Open+Sans:wght@400;700&display=swap" rel="stylesheet">
<style>
  :root {
    --brand-green: #4a8028;
    --ink: #2b2b2b;
    --card: #ffffff;
    --backdrop: #e9e6e3;
  }
  * { margin: 0; padding: 0; box-sizing: border-box; }
  html, body {
    width: 1200px;
    height: 997px;
    overflow: hidden;
    background: var(--backdrop);
    font-family: "Open Sans", Arial, sans-serif;
  }
  .sheet {
    position: relative;
    width: 1200px;
    height: 997px;
  }
  .card {
    position: absolute;
    left: 280px;
    width: 640px;
    height: 366px;
    background: var(--card);
    border-radius: 10px;
    box-shadow: 0 6px 18px rgba(0,0,0,0.10);
    overflow: hidden;
  }
  .card--details { top: 100px; }
  .card--brand {
    top: 530px;
    display: flex;
    align-items: center;
    justify-content: center;
  }

  .company-name {
    display: flex;
    align-items: center;
    gap: 10px;
    color: var(--brand-green);
    font-weight: 700;
    line-height: 1;
    white-space: nowrap;
  }
  .company-name__square {
    flex: none;
    background: var(--brand-green);
  }

  .card--details .company-name {
    position: absolute;
    top: 48px;
    right: 44px;
    font-size: 24px;
  }
  .card--details .company-name__square { width: 16px; height: 16px; }

  .card--brand .company-name { font-size: 38px; gap: 14px; }
  .card--brand .company-name__square { width: 26px; height: 26px; }

  .accent-block {
    position: absolute;
    left: 44px;
    border-left: 7px solid var(--brand-green);
    padding-left: 14px;
  }
  .person { top: 148px; }
  .person__name {
    color: var(--brand-green);
    font-weight: 700;
    font-size: 17px;
    line-height: 1.2;
  }
  .person__title {
    color: var(--brand-green);
    font-size: 13px;
    line-height: 1.3;
  }
  .contacts {
    bottom: 44px;
    list-style: none;
  }
  .contacts li {
    display: flex;
    align-items: center;
    gap: 8px;
    color: var(--ink);
    font-size: 14px;
    line-height: 1.45;
  }
  .contacts svg {
    width: 12px;
    height: 12px;
    flex: none;
    fill: none;
    stroke: var(--brand-green);
    stroke-width: 2;
  }
</style>
</head>
<body>
<main class="sheet">

  <section class="card card--details" aria-label="Business card, details side">
    <p class="company-name">
      <span class="company-name__square" aria-hidden="true"></span>
      Quillmark Homesteads
    </p>

    <div class="accent-block person">
      <p class="person__name">Derek Tolvane</p>
      <p class="person__title">President</p>
    </div>

    <ul class="accent-block contacts">
      <li>
        <svg viewBox="0 0 12 12" aria-hidden="true"><path d="M2 1.5 L4 1.5 L5 4 L3.8 5 Q5 7.5 7 8.2 L8 7 L10.5 8 L10.5 10 Q6 11 2.5 6.5 Q1 4 2 1.5 Z"/></svg>
        0217394062
      </li>
      <li>
        <svg viewBox="0 0 12 12" aria-hidden="true"><rect x="1" y="2.5" width="10" height="7"/><path d="M1 2.5 L6 6.5 L11 2.5"/></svg>
        dtolvane@quillmarkhomesteads.co.nz
      </li>
      <li>
        <svg viewBox="0 0 12 12" aria-hidden="true"><circle cx="6" cy="6" r="5"/><ellipse cx="6" cy="6" rx="2.2" ry="5"/><path d="M1 6 H11"/></svg>
        www.quillmarkhomesteads.co.nz
      </li>
    </ul>
  </section>

  <section class="card card--brand" aria-label="Business card, company side">
    <p class="company-name">
      <span class="company-name__square" aria-hidden="true"></span>
      Quillmark Homesteads
    </p>
  </section>

</main>
</body>
</html>
```